IT Company requires new Business Card design.

Over the years we have had a few different business card designs. We are now due for new cards across the board for all staff. We felt this would be a good time to start fresh with a new design. Our traditional card simply had our details on the front, and a list of services on the back. We don't particularly need the list of services, we have had cards where the only thing on the rear of the card was our logo.
Feel free to be creative, we would like our tag line "Managed IT Services" to appear at some point, doesn't necessarily have to be with the logo.
I have attached samples and drafts of various previous cards we have used over the years.

```html
<!DOCTYPE html>
<html lang="en">
<head>
<meta charset="utf-8">
<title>Bayline Networks – Business Card</title>
<link rel="stylesheet" href="https://fonts.googleapis.com/css2?family=Open+Sans:wght@400;600;700&display=swap">
<style>
  :root {
    --backdrop: #e6e6e4;
    --card: #ffffff;
    --slate: #67737c;
    --slate-dark: #4f5b64;
    --ink: #2b2b2b;
    --rule: #8a949b;
  }
  * { margin: 0; padding: 0; box-sizing: border-box; }
  html, body {
    width: 1034px; height: 1200px; overflow: hidden;
    background: var(--backdrop);
    font-family: "Open Sans", Arial, sans-serif;
    color: var(--ink);
  }
  .canvas { position: relative; width: 1034px; height: 1200px; }
  .card {
    position: absolute; left: 74px; width: 898px; height: 515px;
    background: var(--card);
    box-shadow: 0 2px 6px rgba(0,0,0,0.18);
  }
  .card--front { top: 65px; }
  .card--back { top: 622px; }

  /* Front */
  .rule-top, .rule-bottom {
    position: absolute; left: 0; right: 0; height: 2px; background: var(--rule);
  }
  .rule-top { top: 62px; }
  .rule-bottom { top: 155px; }
  .title-band {
    position: absolute; left: 0; right: 0; top: 72px; height: 74px;
    background: var(--slate);
    display: flex; align-items: center; justify-content: center;
    color: #fff; font-size: 20px; letter-spacing: 0.2px;
  }
  .title-band .person { font-weight: 700; font-size: 25px; margin-right: 6px; }
  .front-brand {
    position: absolute; left: 96px; top: 268px; width: 270px;
    text-align: right; color: var(--slate);
    font-weight: 700; font-size: 40px; line-height: 1.1; letter-spacing: 0.5px;
  }
  .divider {
    position: absolute; left: 387px; top: 209px; width: 2px; height: 249px;
    background: linear-gradient(to bottom, rgba(138,148,155,0.1), var(--rule) 30%, var(--rule) 70%, rgba(138,148,155,0.1));
  }
  .contact-list {
    position: absolute; left: 418px; top: 207px; list-style: none;
    font-size: 20px; line-height: 36px;
  }
  .contact-list li { display: flex; align-items: center; }
  .contact-list svg { width: 20px; height: 20px; margin-right: 12px; fill: var(--slate); flex: none; }
  .address {
    position: absolute; left: 418px; top: 400px;
    font-size: 20px; line-height: 29px; font-style: normal;
  }

  /* Back */
  .brand-mark {
    position: absolute; left: 185px; top: 162px; width: 160px; height: 160px;
    background: var(--slate);
  }
  .brand-name {
    position: absolute; left: 380px; top: 156px;
    color: var(--slate); font-weight: 700; font-size: 66px;
    line-height: 1.05; letter-spacing: 0.5px;
  }
  .tagline {
    position: absolute; left: 0; right: 0; top: 360px; text-align: center;
    color: var(--slate-dark); font-size: 20px; font-weight: 400;
  }
  .web-address {
    position: absolute; left: 0; right: 0; top: 452px; text-align: center;
    font-size: 24px; letter-spacing: 2.5px; color: var(--ink);
  }
</style>
</head>
<body>
<main class="canvas">

  <section class="card card--front" aria-label="Card front">
    <div class="rule-top"></div>
    <div class="title-band"><span class="person">MARCUS HALE,</span> OPERATION MANAGER</div>
    <div class="rule-bottom"></div>

    <div class="front-brand">BAYLINE<br>NETWORKS</div>
    <div class="divider"></div>

    <ul class="contact-list">
      <li>
        <svg viewBox="0 0 20 20" aria-hidden="true"><path d="M10 1a9 9 0 1 0 0 18a9 9 0 1 0 0-18zm0 1.6a7.4 7.4 0 1 1 0 14.8a7.4 7.4 0 1 1 0-14.8zM7 5.5l1.8 2.4-1 1.2c.6 1.3 1.6 2.3 2.9 2.9l1.2-1 2.4 1.8-.9 1.7c-3.9-.3-7-3.4-7.3-7.3z"/></svg>
        08 9300 4100
      </li>
      <li>
        <svg viewBox="0 0 20 20" aria-hidden="true"><path d="M6 1h8a1 1 0 0 1 1 1v16a1 1 0 0 1-1 1H6a1 1 0 0 1-1-1V2a1 1 0 0 1 1-1zm1 2v8h6V3zm0 10v1.5h1.5V13zm2.25 0v1.5h1.5V13zm2.25 0v1.5H13V13zM7 15.5V17h1.5v-1.5zm2.25 0V17h1.5v-1.5zm2.250 0V17H13v-1.5z"/></svg>
        0412 558 019
      </li>
      <li>
        <svg viewBox="0 0 20 20" aria-hidden="true"><path d="M6 1h7l2 2v5H6zM2 9h16a1 1 0 0 1 1 1v7a1 1 0 0 1-1 1H2a1 1 0 0 1-1-1v-7a1 1 0 0 1 1-1zm2 3v2h12v-2z"/></svg>
        08 9300 4100
      </li>
      <li>
        <svg viewBox="0 0 20 20" aria-hidden="true"><path d="M2 5l8-3 8 3v11a1 1 0 0 1-1 1H3a1 1 0 0 1-1-1zm1.6 1.4L10 11l6.4-4.6L10 4z"/></svg>
        marcus@baylinenetworks.com.au
      </li>
      <li>
        <svg viewBox="0 0 20 20" aria-hidden="true"><path d="M10 1a9 9 0 1 0 0 18a9 9 0 1 0 0-18zm-1 2.2C7.6 4.6 6.9 6.6 6.8 9H3.1A7 7 0 0 1 9 3.2zm2 0A7 7 0 0 1 16.9 9h-3.7c-.1-2.4-.8-4.4-2.2-5.8zM8.8 9c.1-2 .5-3.6 1.2-4.8.7 1.2 1.1 2.8 1.2 4.8zM3.1 11h3.7c.1 2.4.8 4.4 2.2 5.8A7 7 0 0 1 3.1 11zm5.7 0h2.4c-.1 2-.5 3.6-1.2 4.8-.7-1.2-1.1-2.8-1.2-4.8zm4.4 0h3.7A7 7 0 0 1 11 16.8c1.4-1.4 2.1-3.4 2.2-5.8z"/></svg>
        www.baylinenetworks.com.au
      </li>
    </ul>

    <address class="address">
      Unit 4 18 Harbour Way<br>
      Kellerton WA 6170
    </address>
  </section>

  <section class="card card--back" aria-label="Card back">
    <div class="brand-mark"></div>
    <div class="brand-name">BAYLINE<br>NETWORKS</div>
    <div class="tagline">Managed IT Services</div>
    <div class="web-address">www.baylinenetworks.com.au</div>
  </section>

</main>
</body>
</html>
```